Accounting firm needing business card / letterhead designed
Marcus L. Trenholm, CPA
marcus@veltrowledger.com
www.veltrowledger.com
842 E Alder Ave Perrysburg, OH 43827
419-562-0974

```html
<!DOCTYPE html>
<html lang="en">
<head>
<meta charset="utf-8">
<title>Veltrow Ledger – Business Card</title>
<link rel="stylesheet" href="https://fonts.googleapis.com/css2?family=Open+Sans:wght@400;600;700&display=swap">
<style>
  :root {
    --navy: #252063;
    --green: #7dc142;
    --white: #ffffff;
    --paper: #f1f1f1;
    --backdrop: #2a2a2a;
    --soft-text: #e6e6ee;
  }
  * { box-sizing: border-box; margin: 0; padding: 0; }
  html, body { width: 1200px; height: 904px; overflow: hidden; }
  body {
    background: var(--backdrop);
    font-family: "Open Sans", Arial, sans-serif;
    display: flex;
    flex-direction: column;
    align-items: center;
    justify-content: center;
    gap: 36px;
  }
  .card {
    width: 700px;
    height: 400px;
    position: relative;
    overflow: hidden;
    box-shadow: 0 10px 30px rgba(0,0,0,.45);
  }

  /* Back side */
  .card-back {
    background: var(--navy);
    display: flex;
    align-items: center;
    justify-content: center;
  }
  .brand-name {
    font-weight: 700;
    text-transform: uppercase;
    letter-spacing: 6px;
    font-size: 40px;
    line-height: 1;
  }
  .card-back .brand-name { color: var(--white); }

  /* Front side */
  .card-front { background: var(--navy); }
  .front-top {
    height: 205px;
    background: linear-gradient(180deg, var(--white) 0%, var(--paper) 100%);
    display: flex;
    align-items: center;
    justify-content: center;
    padding-top: 10px;
  }
  .card-front .brand-name { color: var(--navy); }
  .accent-rule {
    height: 6px;
    background: var(--green);
    margin-top: 8px;
  }
  .front-bottom {
    display: flex;
    align-items: center;
    height: 181px;
    padding: 0 40px 0 60px;
  }
  .holder-name {
    color: var(--white);
    font-weight: 700;
    font-size: 24px;
    width: 300px;
    padding-top: 40px;
  }
  .divider {
    width: 1px;
    height: 120px;
    background: var(--soft-text);
    opacity: .8;
    margin: 0 26px 0 10px;
  }
  .contact-list {
    list-style: none;
    color: var(--soft-text);
    font-size: 15px;
    line-height: 1.35;
  }
  .contact-list li { display: flex; align-items: center; gap: 10px; }
  .contact-list .address { padding-left: 0; margin-bottom: 2px; }
  .contact-icon { width: 15px; height: 15px; flex: none; }
</style>
</head>
<body>

  <section class="card card-back" aria-label="Card back">
    <span class="brand-name">Veltrow Ledger</span>
  </section>

  <section class="card card-front" aria-label="Card front">
    <div class="front-top">
      <span class="brand-name">Veltrow Ledger</span>
    </div>
    <div class="accent-rule"></div>
    <div class="front-bottom">
      <p class="holder-name">Marcus L. Trenholm, CPA</p>
      <div class="divider"></div>
      <ul class="contact-list">
        <li class="address">842 E Alder Ave Perrysburg<br>OH 43827</li>
        <li>
          <svg class="contact-icon" viewBox="0 0 24 24" fill="none" stroke="currentColor" stroke-width="2" stroke-linecap="round" stroke-linejoin="round" aria-hidden="true">
            <path d="M22 16.9v3a2 2 0 0 1-2.2 2 19.8 19.8 0 0 1-8.6-3.1 19.5 19.5 0 0 1-6-6A19.8 19.8 0 0 1 2.1 4.2 2 2 0 0 1 4.1 2h3a2 2 0 0 1 2 1.7c.1.9.4 1.8.7 2.7a2 2 0 0 1-.5 2.1L8 9.8a16 16 0 0 0 6 6l1.3-1.3a2 2 0 0 1 2.1-.4c.9.3 1.8.6 2.7.7a2 2 0 0 1 1.7 2z"/>
          </svg>
          419-562-0974
        </li>
        <li>
          <svg class="contact-icon" viewBox="0 0 24 24" fill="none" stroke="currentColor" stroke-width="2" stroke-linejoin="round" aria-hidden="true">
            <rect x="2" y="5" width="20" height="14" rx="1"/>
            <path d="M2 6l10 7 10-7"/>
          </svg>
          marcus@veltrowledger.com
        </li>
        <li>
          <svg class="contact-icon" viewBox="0 0 24 24" fill="none" stroke="currentColor" stroke-width="2" aria-hidden="true">
            <circle cx="12" cy="12" r="10"/>
            <path d="M2 12h20M12 2a15 15 0 0 1 0 20M12 2a15 15 0 0 0 0 20"/>
          </svg>
          www.veltrowledger.com
        </li>
      </ul>
    </div>
  </section>

</body>
</html>
```